Postcard design to acquire new clients for my Property Management Company

I'm looking for a postcard design that I can send to prospective clients detailing information about my company and services.
Postcard should be eye catching and contain information from www.bramblecrestpm.com. I've provided a few screen shots for the most important information and my logo.
Target Market(s)
Real Estate
Industry/Entity Type
Real Estate
Font styles to use
Sans Serif
Requirements
Must have
- Must be eye catching!! this will be a direct mail piece - I'd like for the card to be read and not tossed in the trash immediately.
Design que from the logo.
A place to write / print the receipts name and address.
our physical address - 2387 Hollow Pine Road, Lubbock, TX 79852.
Should not have
- the contact information on the business card is not accurate - please use info from website.

```html
<!DOCTYPE html>
<html lang="en">
<head>
<meta charset="utf-8">
<title>Bramblecrest Property Management – Postcard</title>
<link href="https://fonts.googleapis.com/css2?family=Montserrat:wght@300;400;500;600;700;800&family=Arimo:wght@400&display=swap" rel="stylesheet">
<style>
  :root {
    --brand-blue: #1f5b92;
    --brand-navy: #174a7a;
    --text-gray: #8c8c8c;
    --text-light: #a3a3a3;
    --card-white: #ffffff;
    --canvas-bg: #efefef;
    --rule: #222222;
  }
  * { margin: 0; padding: 0; box-sizing: border-box; }
  html, body { width: 1005px; height: 1200px; overflow: hidden; }
  body {
    background: var(--canvas-bg);
    font-family: "Montserrat", Arial, sans-serif;
    position: relative;
  }
  .postcard {
    position: absolute;
    left: 82px;
    width: 840px;
    height: 560px;
    background: var(--card-white);
    box-shadow: 0 6px 14px rgba(0,0,0,0.18);
    overflow: hidden;
  }
  .postcard--front { top: 30px; }
  .postcard--back { top: 610px; }

  /* brand name */
  .brand-name {
    position: absolute;
    color: var(--brand-navy);
    font-weight: 700;
    line-height: 1.15;
    letter-spacing: 5px;
  }
  .brand-name__line { display: block; }
  .brand-name__line--main { font-size: 36px; letter-spacing: 7px; }
  .brand-name__line--sub { font-size: 17px; letter-spacing: 5.4px; }

  /* FRONT */
  .front__brand { left: 40px; top: 30px; }
  .front__art { position: absolute; inset: 0; }
  .headline {
    position: absolute;
    left: 46px;
    top: 146px;
    color: var(--brand-blue);
    font-size: 34px;
    line-height: 43px;
  }
  .headline__light { font-weight: 400; display: block; }
  .headline__bold { font-weight: 800; display: block; }
  .headline__rule {
    width: 100px;
    height: 3px;
    background: var(--brand-navy);
    margin-top: 4px;
  }
  .plans {
    position: absolute;
    left: 44px;
    top: 350px;
    list-style: none;
  }
  .plan {
    display: flex;
    align-items: center;
    height: 50px;
    margin-bottom: 4px;
  }
  .plan__rate {
    width: 46px;
    height: 46px;
    border: 2px solid var(--brand-navy);
    border-radius: 50%;
    display: flex;
    align-items: center;
    justify-content: center;
    color: var(--brand-navy);
    font-weight: 700;
    font-size: 17px;
    letter-spacing: -1px;
    margin-right: 18px;
  }
  .plan__title {
    display: block;
    color: var(--text-gray);
    font-weight: 600;
    font-size: 16px;
  }
  .plan__note {
    display: block;
    color: var(--text-light);
    font-size: 10.5px;
    margin-top: 1px;
  }

  /* BACK */
  .back__heading {
    position: absolute;
    left: 48px;
    top: 38px;
    color: var(--brand-blue);
    font-weight: 700;
    font-size: 23px;
  }
  .back__intro {
    position: absolute;
    left: 50px;
    top: 68px;
    color: var(--text-light);
    font-size: 12.5px;
    line-height: 16px;
    text-transform: uppercase;
  }
  .services {
    position: absolute;
    left: 46px;
    top: 128px;
    width: 440px;
    list-style: none;
    display: grid;
    grid-template-columns: 215px 215px;
    row-gap: 18px;
  }
  .service {
    display: flex;
    align-items: center;
    height: 66px;
  }
  .service__icon {
    width: 66px;
    height: 66px;
    flex: none;
    margin-right: 12px;
  }
  .service__label {
    color: var(--text-gray);
    font-size: 15.5px;
    line-height: 19px;
  }
  .back__brand { left: 48px; top: 476px; }
  .back__brand .brand-name__line--main { font-size: 34px; letter-spacing: 6.4px; }
  .back__brand .brand-name__line--sub { font-size: 16px; letter-spacing: 5px; }

  .indicia {
    position: absolute;
    left: 688px;
    top: 80px;
    width: 100px;
    height: 98px;
    border: 1px solid var(--rule);
    font-family: "Arimo", Arial, sans-serif;
    font-size: 13px;
    line-height: 15.5px;
    text-align: center;
    padding-top: 10px;
    color: #111;
  }
  .address-window {
    position: absolute;
    left: 520px;
    top: 210px;
    width: 268px;
    height: 70px;
    border: 2px solid var(--rule);
  }
  .contact__heading {
    position: absolute;
    left: 520px;
    top: 400px;
    color: var(--brand-blue);
    font-weight: 700;
    font-size: 19px;
  }
  .contact__list {
    position: absolute;
    left: 520px;
    top: 445px;
    list-style: none;
  }
  .contact__item {
    display: flex;
    align-items: center;
    color: var(--text-light);
    font-size: 11.5px;
    height: 14px;
  }
  .contact__item svg { width: 10px; height: 10px; margin-right: 10px; }
  .contact__address {
    position: absolute;
    left: 520px;
    top: 510px;
    color: var(--text-light);
    font-size: 11.5px;
  }
</style>
</head>
<body>

<!-- FRONT -->
<section class="postcard postcard--front">
  <svg class="front__art" width="840" height="560" viewBox="0 0 840 560">
    <defs>
      <linearGradient id="photoTone" x1="0" y1="0" x2="1" y2="1">
        <stop offset="0" stop-color="#c9d6df"/>
        <stop offset="0.45" stop-color="#4d6a8a"/>
        <stop offset="0.8" stop-color="#2c3e55"/>
        <stop offset="1" stop-color="#7f9aa6"/>
      </linearGradient>
    </defs>
    <polygon points="541,0 840,0 840,560 320,560" fill="url(#photoTone)" role="img" aria-label="Photo of two smiling businessmen in suits on a sofa reviewing a laptop beside a glass coffee table"/>
    <polygon points="514,0 541,0 320,560 278,560" fill="var(--brand-navy)"/>
  </svg>

  <h2 class="brand-name front__brand">
    <span class="brand-name__line brand-name__line--main">BRAMBLECREST</span>
    <span class="brand-name__line brand-name__line--sub">PROPERTY MANAGEMENT</span>
  </h2>

  <h1 class="headline">
    <span class="headline__light">CHOOSE THE</span>
    <span class="headline__bold">RIGHT PROPERTY</span>
    <span class="headline__bold">MANAGEMENT</span>
    <span class="headline__light">SYSTEM</span>
    <div class="headline__rule"></div>
  </h1>

  <ul class="plans">
    <li class="plan">
      <span class="plan__rate">9%</span>
      <span><span class="plan__title">LEASE ONLY</span><span class="plan__note">You Just Need Tenants</span></span>
    </li>
    <li class="plan">
      <span class="plan__rate">10%</span>
      <span><span class="plan__title">FULL SERVICE</span><span class="plan__note">Our Most Popular</span></span>
    </li>
    <li class="plan">
      <span class="plan__rate">12%</span>
      <span><span class="plan__title">PREMIUM SERVICE</span><span class="plan__note">Our Premier Service</span></span>
    </li>
  </ul>
</section>

<!-- BACK -->
<section class="postcard postcard--back">
  <h2 class="back__heading">DISCOVER OUR SERVICES</h2>
  <p class="back__intro">We offer full-service property<br>management solutions</p>

  <ul class="services">
    <li class="service">
      <svg class="service__icon" viewBox="0 0 66 66"><circle cx="33" cy="33" r="31" fill="none" stroke="var(--brand-navy)" stroke-width="3"/><path d="M15 34 L33 18 L51 34 L47 34 L47 48 L38 48 L38 38 L28 38 L28 48 L19 48 L19 34 Z" fill="var(--brand-navy)"/><rect x="41" y="20" width="5" height="9" fill="var(--brand-navy)"/></svg>
      <span class="service__label">Property<br>Marketing</span>
    </li>
    <li class="service">
      <svg class="service__icon" viewBox="0 0 66 66"><circle cx="33" cy="33" r="31" fill="none" stroke="var(--brand-navy)" stroke-width="3"/><circle cx="29" cy="29" r="12" fill="none" stroke="var(--brand-navy)" stroke-width="5"/><line x1="38" y1="38" x2="49" y2="49" stroke="var(--brand-navy)" stroke-width="7" stroke-linecap="round"/></svg>
      <span class="service__label">Property<br>Inspections</span>
    </li>
    <li class="service">
      <svg class="service__icon" viewBox="0 0 66 66"><circle cx="33" cy="33" r="31" fill="none" stroke="var(--brand-navy)" stroke-width="3"/><circle cx="27" cy="25" r="7" fill="var(--brand-navy)"/><circle cx="40" cy="24" r="6" fill="var(--brand-navy)"/><path d="M14 46 Q14 34 27 34 Q40 34 40 46 Z" fill="var(--brand-navy)"/><path d="M38 33 Q52 32 52 44 L42 44 Q42 37 38 33 Z" fill="var(--brand-navy)"/></svg>
      <span class="service__label">Tenant<br>Screening</span>
    </li>
    <li class="service">
      <svg class="service__icon" viewBox="0 0 66 66"><circle cx="33" cy="33" r="31" fill="none" stroke="var(--brand-navy)" stroke-width="3"/><g fill="var(--brand-navy)"><rect x="18" y="34" width="5" height="13"/><rect x="26" y="30" width="5" height="17"/><rect x="34" y="33" width="5" height="14"/><rect x="42" y="27" width="5" height="20"/></g><polyline points="17,28 28,21 36,26 49,17" fill="none" stroke="var(--brand-navy)" stroke-width="2.5"/></svg>
      <span class="service__label">Financial<br>Reporting</span>
    </li>
    <li class="service">
      <svg class="service__icon" viewBox="0 0 66 66"><circle cx="33" cy="33" r="31" fill="none" stroke="var(--brand-navy)" stroke-width="3"/><path d="M14 32 L33 15 L52 32 L47 32 L47 50 L19 50 L19 32 Z" fill="var(--brand-navy)"/><text x="33" y="46" text-anchor="middle" font-family="Montserrat, sans-serif" font-weight="700" font-size="17" fill="#fff">$</text></svg>
      <span class="service__label">Rent<br>Collection</span>
    </li>
    <li class="service">
      <svg class="service__icon" viewBox="0 0 66 66"><circle cx="33" cy="33" r="31" fill="none" stroke="var(--brand-navy)" stroke-width="3"/><g stroke="var(--brand-navy)" stroke-width="3" fill="none"><line x1="33" y1="16" x2="33" y2="47"/><line x1="18" y1="22" x2="48" y2="22"/><line x1="20" y1="22" x2="14" y2="36"/><line x1="20" y1="22" x2="26" y2="36"/><line x1="46" y1="22" x2="40" y2="36"/><line x1="46" y1="22" x2="52" y2="36"/></g><g fill="var(--brand-navy)"><path d="M13 36 L27 36 Q20 44 13 36 Z"/><path d="M39 36 L53 36 Q46 44 39 36 Z"/><rect x="24" y="47" width="18" height="4"/></g></svg>
      <span class="service__label">Legal<br>Guidance</span>
    </li>
    <li class="service">
      <svg class="service__icon" viewBox="0 0 66 66"><circle cx="33" cy="33" r="31" fill="none" stroke="var(--brand-navy)" stroke-width="3"/><circle cx="30" cy="31" r="11" fill="none" stroke="var(--brand-navy)" stroke-width="5" stroke-dasharray="5 3"/><circle cx="30" cy="31" r="4" fill="var(--brand-navy)"/><line x1="22" y1="47" x2="47" y2="20" stroke="var(--brand-navy)" stroke-width="5" stroke-linecap="round"/></svg>
      <span class="service__label">Maintenance</span>
    </li>
    <li class="service">
      <svg class="service__icon" viewBox="0 0 66 66"><circle cx="33" cy="33" r="31" fill="none" stroke="var(--brand-navy)" stroke-width="3"/><path d="M33 14 L49 20 L49 32 Q49 45 33 53 Q17 45 17 32 L17 20 Z" fill="none" stroke="var(--brand-navy)" stroke-width="3.5"/><path d="M33 19 L33 48 Q21 42 21 32 L21 23 Z" fill="var(--brand-navy)"/></svg>
      <span class="service__label">Evictions</span>
    </li>
  </ul>

  <h2 class="brand-name back__brand">
    <span class="brand-name__line brand-name__line--main">BRAMBLECREST</span>
    <span class="brand-name__line brand-name__line--sub">PROPERTY MANAGEMENT</span>
  </h2>

  <div class="indicia">PRSRT STD<br>ECRWSS<br>U.S.POSTAGE<br>PAID<br>EDDM RETAIL</div>
  <div class="address-window" aria-label="Recipient name and address"></div>

  <h3 class="contact__heading">CONTACT OUR TEAM</h3>
  <ul class="contact__list">
    <li class="contact__item"><svg viewBox="0 0 10 10"><circle cx="5" cy="5" r="4.5" fill="none" stroke="var(--brand-navy)"/><path d="M3 2.5 L4.2 2.5 L4.6 4 L4 4.6 Q4.8 6 5.6 6.2 L6.2 5.6 L7.5 6 L7.5 7.2 Q4 7.5 3 2.5 Z" fill="var(--brand-navy)"/></svg>(806) 555-0147</li>
    <li class="contact__item"><svg viewBox="0 0 10 10"><circle cx="5" cy="5" r="4.5" fill="var(--brand-navy)"/><rect x="2.5" y="3.3" width="5" height="3.4" fill="#fff"/></svg>info@bramblecrestpm.com</li>
    <li class="contact__item"><svg viewBox="0 0 10 10"><circle cx="5" cy="5" r="4.5" fill="var(--brand-navy)"/><circle cx="5" cy="5" r="2.2" fill="none" stroke="#fff" stroke-width="0.8"/></svg>www.bramblecrestpm.com</li>
  </ul>
  <p class="contact__address">2387 Hollow Pine Road, Lubbock, TX 79852</p>
</section>

</body>
</html>
```